Business card design for a dynamic IT consulting company

We need a business card design for a young firm, specialized in the Telecommunications/Consulting industry. The name of the company is Quindor and Partners Business Consulting Ltd. (Short name: Quindor and Partnes)
Quindor = solve read reverse, so we aim to be uncomplicated and solution-oriented. The small pipe in our logo is also related to the word solve. So we need a new business card design, which is simple, eye catching and something non traditional (I would probably prefer a square shaped design rather than a rectangle, but open for suggestions). Attached our logo.

Target Market(s)

Usually our customers are Tier1 Telecoms providers (Q-Netra, Palorix, etc) and their executives.

Industry/Entity Type

Business

Contact Information for Business Card

Name: Bence Tolnavari
Email: b.tolnavari@quindor.hu
Web: www.quindor.hu
Mobile: +36 30 518 2769
Title: Managing Director

Optional:
Company name: Quindor and Partners Ltd.
Address: 1087 Budapest, Tolvenka str. 28/C, Hungary

Font styles to use
Other font styles liked:
• helveticaneue_medium, Prime Regular are used now.

Colors

Designer to choose colors to be used in the design.

Requirements
Must have
• I would like to have a 2 sided design.
Nice to have
• I thought if we make the logo a bit bigger (without the company name), that could go to the back with the company name below. I though, if the pipe in the logo is somehow touchable on the business card, would be nice and unique.

```html
<!DOCTYPE html>
<html lang="en">
<head>
<meta charset="utf-8">
<title>Quindor and Partners – Business Card</title>
<link href="https://fonts.googleapis.com/css2?family=Exo+2:wght@400;700&family=Open+Sans:wght@400;600&display=swap" rel="stylesheet">
<style>
  :root {
    --stage: #222222;
    --paper: #ffffff;
    --brand-blue: #1a9ad6;
    --brand-magenta: #b3268f;
    --ink: #2b2b2b;
    --ink-soft: #5a5a5a;
    --back-blue: #0f9ad8;
  }
  * { margin: 0; padding: 0; box-sizing: border-box; }
  html, body { width: 1200px; height: 900px; overflow: hidden; background: var(--stage); }
  .stage { position: relative; width: 1200px; height: 900px; }

  .card { position: absolute; top: 306px; width: 440px; height: 271px; overflow: hidden; }
  .card-front { left: 149px; background: var(--paper); font-family: "Open Sans", sans-serif; color: var(--ink); }
  .card-back { left: 608px; background: var(--back-blue); }

  .accent-marks { position: absolute; left: 0; top: 26px; }
  .holder { position: absolute; left: 40px; top: 29px; }
  .holder-name { font-family: "Exo 2", sans-serif; font-weight: 700; font-size: 14.5px; color: var(--brand-blue); letter-spacing: 0.3px; line-height: 18px; }
  .holder-title { font-size: 11.5px; color: var(--ink); line-height: 15px; }

  .brand { position: absolute; left: 100px; top: 100px; display: flex; align-items: center; gap: 12px; }
  .brand-square { width: 14px; height: 14px; background: var(--brand-blue); }
  .brand-name { font-family: "Exo 2", sans-serif; font-weight: 400; font-size: 31px; color: var(--ink-soft); letter-spacing: 0.5px; }

  .contacts { position: absolute; left: 22px; top: 195px; list-style: none; font-size: 11.5px; line-height: 16px; }
  .contacts li { display: flex; align-items: center; gap: 4px; }
  .contacts svg { width: 10px; height: 10px; flex: none; }

  .address { position: absolute; right: 22px; top: 194px; text-align: right; font-size: 11.5px; line-height: 16px; }
  .address-company { color: var(--brand-blue); font-size: 12px; }

  .bottom-band { position: absolute; left: 0; bottom: 0; }

  .back-pattern { position: absolute; inset: 0; background: linear-gradient(180deg, #17a0dc 0%, #0c95d3 100%); }
  .back-brand { position: absolute; inset: 0; display: flex; align-items: center; justify-content: center; font-family: "Exo 2", sans-serif; font-size: 24px; color: #ffffff; letter-spacing: 0.5px; }
</style>
</head>
<body>
<main class="stage">

  <section class="card card-front" aria-label="Business card front">
    <svg class="accent-marks" width="30" height="38" viewBox="0 0 30 38">
      <polygon points="0,0 11,0 16,37 0,37" fill="var(--brand-magenta)"/>
      <polygon points="11,0 28,0 28,37 16,37" fill="var(--brand-blue)"/>
    </svg>

    <div class="holder">
      <p class="holder-name">BENCE TOLNAVARI</p>
      <p class="holder-title">Managing Director</p>
    </div>

    <div class="brand">
      <span class="brand-square" aria-hidden="true"></span>
      <span class="brand-name">Quindor &amp; Partners</span>
    </div>

    <ul class="contacts">
      <li>
        <svg viewBox="0 0 10 10" aria-hidden="true"><path d="M1 3 Q5 0 9 3 L8 4.5 L6.5 3.5 L3.5 3.5 L2 4.5 Z M2.5 5 H7.5 L8.5 8.5 H1.5 Z" fill="var(--brand-blue)"/></svg>
        +36 30 518 2769
      </li>
      <li>
        <svg viewBox="0 0 10 10" aria-hidden="true"><rect x="0.5" y="2" width="9" height="6.5" fill="var(--brand-blue)"/><path d="M0.5 2 L5 5.5 L9.5 2" stroke="#fff" stroke-width="0.9" fill="none"/></svg>
        b.tolnavari@quindor.hu
      </li>
      <li>
        <svg viewBox="0 0 10 10" aria-hidden="true"><circle cx="5" cy="5" r="4.5" fill="var(--brand-blue)"/><path d="M5 0.5 V9.5 M0.5 5 H9.5" stroke="#fff" stroke-width="0.7"/></svg>
        www.quindor.hu
      </li>
    </ul>

    <div class="address">
      <p class="address-company">Quindor and Partners Ltd</p>
      <p>1087 Budapest, Tolvenka</p>
      <p>str. 28/C, Hungary</p>
    </div>

    <svg class="bottom-band" width="440" height="20" viewBox="0 0 440 20">
      <polygon points="0,6 217,6 208,20 0,20" fill="var(--brand-magenta)"/>
      <polygon points="222,1 440,1 440,20 207,20" fill="var(--brand-blue)"/>
    </svg>
  </section>

  <section class="card card-back" aria-label="Business card back">
    <div class="back-pattern" role="img" aria-label="Faint repeating brand pattern in blue tones"></div>
    <p class="back-brand">Quindor &amp; Partners</p>
  </section>

</main>
</body>
</html>
```